Web Developer Needs a Business Card Design

I need a personal business card design that represents me as a web developer for potential employers. I would like the background to be a dark color on the front for contrast with my logo and name. The back will have all my information along with a smaller version of the logo. I want something with a modern look and feel, not too conservative. This will be used for potential employers and freelance work.

Industry/Entity Type

Business

Contact Information for Business Card

Front should have my logo and name. The back should have all my personal information which would include: name: Tom Varulek, phone: 570-614-3098, email: tomvarulek@quillbox.net, website url: www.tomvarulek.net, logo, web developer.

Font styles to use
Sans Serif

Requirements
Must have
• Must include my logo. The color palette base color will be the logo color.

```html
<!DOCTYPE html>
<html lang="en">
<head>
<meta charset="utf-8">
<title>Tom Varulek – Business Card</title>
<link rel="stylesheet" href="https://fonts.googleapis.com/css2?family=Open+Sans:wght@400;600&display=swap">
<style>
  :root {
    --teal: #8fdad0;
    --teal-light: #a6e6dc;
    --teal-deep: #7ccfc3;
    --paper: #ffffff;
    --paper-shade: #ececec;
    --ink: #111111;
    --stage: #e9e6e1;
  }
  * { box-sizing: border-box; margin: 0; padding: 0; }
  html, body {
    width: 1200px; height: 892px; overflow: hidden;
    background: var(--stage);
    font-family: "Open Sans", sans-serif;
    color: var(--ink);
  }
  .canvas {
    position: relative; width: 1200px; height: 892px;
    display: flex; align-items: center; justify-content: center; gap: 60px;
  }
  .card {
    position: relative; width: 520px; height: 297px;
    background: var(--paper);
    box-shadow: 0 6px 18px rgba(0,0,0,0.18);
    overflow: hidden;
  }

  /* Front card */
  .card-front { display: flex; }
  .front-mark-panel {
    position: relative; width: 40%; height: 100%;
    background: linear-gradient(180deg, var(--paper), var(--paper-shade));
    display: flex; align-items: center; justify-content: center;
  }
  .edge-tab {
    position: absolute; left: 0; top: 44px; bottom: 0; width: 14px;
    background: var(--teal-deep);
    border-top-right-radius: 7px;
  }
  .front-info-panel {
    position: relative; width: 60%; height: 100%;
    background: linear-gradient(160deg, var(--teal-light), var(--teal));
    padding: 30px 26px;
  }
  .holder-name { font-size: 31px; font-weight: 400; line-height: 1.1; letter-spacing: 0.5px; }
  .holder-role { font-size: 16px; margin-top: 2px; }
  .contact-list {
    position: absolute; right: 22px; bottom: 26px;
    list-style: none; font-size: 14px; line-height: 1.55;
  }
  .contact-list li { display: flex; align-items: center; gap: 9px; }
  .contact-icon {
    width: 13px; height: 13px; background: var(--ink);
    display: inline-flex; align-items: center; justify-content: center; flex: none;
  }

  /* Brand mark stand-in */
  .brand-mark {
    width: 168px; height: 168px; border-radius: 50%;
    border: 7px solid var(--teal);
    display: flex; align-items: center; justify-content: center; text-align: center;
  }
  .brand-name { font-size: 22px; font-weight: 600; color: var(--teal-deep); line-height: 1.15; }

  /* Back card */
  .card-back {
    display: flex; align-items: center; justify-content: space-between;
    padding: 0 56px 0 44px;
    background: linear-gradient(180deg, var(--paper), var(--paper-shade));
  }
  .back-name { font-size: 30px; font-weight: 400; letter-spacing: 0.5px; }
</style>
</head>
<body>
<main class="canvas">
  <section class="card card-front" aria-label="Business card front">
    <div class="front-mark-panel">
      <span class="edge-tab"></span>
      <div class="brand-mark"><span class="brand-name">Tom<br>Varulek</span></div>
    </div>
    <div class="front-info-panel">
      <h1 class="holder-name">Tom Varulek</h1>
      <p class="holder-role">web developer</p>
      <ul class="contact-list">
        <li><span class="contact-icon"><svg width="9" height="9" viewBox="0 0 10 10"><path d="M2 1 L4 3 L3 4 Q4 6 6 7 L7 6 L9 8 L8 9 Q3 9 1 2 Z" fill="#fff"/></svg></span>570-614-3098</li>
        <li><span class="contact-icon"><svg width="9" height="9" viewBox="0 0 10 10"><circle cx="5" cy="5" r="3.6" fill="none" stroke="#fff" stroke-width="1.2"/><path d="M1.4 5 H8.6" stroke="#fff" stroke-width="1"/></svg></span>www.tomvarulek.net</li>
        <li><span class="contact-icon"><svg width="9" height="9" viewBox="0 0 10 10"><rect x="1" y="2.5" width="8" height="5.5" fill="none" stroke="#fff" stroke-width="1"/><path d="M1 2.5 L5 6 L9 2.5" fill="none" stroke="#fff" stroke-width="1"/></svg></span>tomvarulek@quillbox.net</li>
      </ul>
    </div>
  </section>

  <section class="card card-back" aria-label="Business card back">
    <p class="back-name">Tom Varulek</p>
    <div class="brand-mark"><span class="brand-name">Tom<br>Varulek</span></div>
  </section>
</main>
</body>
</html>
```